U.S. Popcorn company needs business cards

We are a popcorn company that manufactures popcorn and sells it to grocery stores worldwide. Our theme is "Americana" and our logo is U.S. route 66 which is the most famous highway in the U.S.

We would like the design to be simple and to use both sides. On the back side we would like to see just the logo and website. The front would be normal details

Target Market(s)

Wholesalers, grocers and distributors

Industry/Entity Type

Manufacture

Contact Information for Business Card

Business name: Prairie Lantern Popcorn
Phone: +1 555 308 4726
Email: Dale@prairielanternpopcorn.com
website: www.prairielanternpopcorn.com
Tag Line: "POPular for a reason"
Name: Dale Whitcombe
Title: Founder/President

Requirements
Must have
• Either this design should be fun or clean and simple. I will let you show me your thougths.
Nice to have
• Anything that ties in the real Hwy Route 66.
• Colors might need to be red, white and blue incorporated.
Should not have
• Not be too busy.

```html
<!DOCTYPE html>
<html lang="en">
<head>
<meta charset="utf-8">
<title>Prairie Lantern Popcorn – Business Cards</title>
<link rel="stylesheet" href="https://fonts.googleapis.com/css2?family=Open+Sans:wght@400;600;700&family=Crimson+Text:wght@400&display=swap">
<style>
  :root {
    --navy: #0c2a6b;
    --red: #e01e26;
    --white: #ffffff;
    --band: #e9f0f3;
    --paper: #f4f4f4;
    --ink: #222222;
    --stage: #d9d9d9;
  }
  * { margin: 0; padding: 0; box-sizing: border-box; }
  html, body { width: 1200px; height: 900px; overflow: hidden; }
  body {
    background: var(--stage);
    font-family: "Open Sans", Arial, sans-serif;
    position: relative;
  }
  .card {
    position: absolute;
    width: 525px;
    height: 300px;
    border-radius: 26px;
    overflow: hidden;
    box-shadow: 0 6px 18px rgba(0,0,0,0.18);
  }
  .card-front { left: 50px; top: 300px; background: var(--red); }
  .card-back { left: 625px; top: 300px; background: var(--paper); }

  .front-shape { position: absolute; inset: 0; width: 100%; height: 100%; }

  .person {
    position: absolute;
    left: 30px;
    top: 118px;
    width: 180px;
    color: var(--white);
  }
  .person-name {
    font-weight: 600;
    font-size: 16px;
    letter-spacing: 0.05em;
    text-transform: uppercase;
    white-space: nowrap;
  }
  .person-title {
    font-size: 13px;
    letter-spacing: 0.04em;
    text-transform: uppercase;
    margin-top: 1px;
  }

  .contact {
    position: absolute;
    right: 28px;
    top: 26px;
    list-style: none;
    color: var(--white);
    font-size: 13px;
    text-align: right;
  }
  .contact li { display: flex; align-items: center; justify-content: flex-end; gap: 7px; line-height: 22px; }
  .contact svg { width: 11px; height: 11px; fill: var(--white); }

  .brand-name {
    position: absolute;
    font-weight: 700;
    text-align: center;
    line-height: 1.1;
  }
  .card-front .brand-name {
    left: 235px; top: 128px; width: 190px;
    color: var(--white);
    font-size: 20px;
  }
  .card-back .brand-name {
    left: 112px; top: 62px; width: 300px;
    color: var(--navy);
    font-size: 28px;
  }
  .tagline {
    position: absolute;
    left: 0; right: 0; top: 170px;
    text-align: center;
    font-family: "Crimson Text", Georgia, serif;
    color: var(--red);
    font-size: 19px;
    letter-spacing: 0.04em;
  }
  .website {
    position: absolute;
    left: 0; right: 0; top: 222px;
    text-align: center;
    color: var(--ink);
    font-size: 13px;
  }
</style>
</head>
<body>

<section class="card card-front" aria-label="Business card front">
  <svg class="front-shape" viewBox="0 0 525 300" preserveAspectRatio="none" aria-hidden="true">
    <path d="M0,0 H525 V110 C480,150 430,174 395,186 C365,194 345,202 330,221 C317,204 295,196 262,196 C160,196 60,200 0,185 Z" fill="var(--band)"/>
    <path d="M0,0 H525 V96 C480,136 430,160 395,172 C365,180 345,188 330,207 C317,190 295,182 262,182 C160,182 60,186 0,171 Z" fill="var(--navy)"/>
  </svg>

  <ul class="contact">
    <li>+1 555 308 4726
      <svg viewBox="0 0 24 24" aria-hidden="true"><path d="M6.6 10.8a15 15 0 0 0 6.6 6.6l2.2-2.2c.3-.3.7-.4 1-.2 1.1.4 2.3.6 3.6.6.6 0 1 .4 1 1V20c0 .6-.4 1-1 1A17 17 0 0 1 3 4c0-.6.4-1 1-1h3.5c.6 0 1 .4 1 1 0 1.3.2 2.5.6 3.6.1.3 0 .7-.2 1z"/></svg>
    </li>
    <li>Dale@prairielanternpopcorn.com
      <svg viewBox="0 0 24 24" aria-hidden="true"><path d="M2 5h20v14H2z M3 6l9 7 9-7" fill="var(--white)" stroke="var(--navy)" stroke-width="1.5"/></svg>
    </li>
  </ul>

  <div class="person">
    <p class="person-name">Dale Whitcombe</p>
    <p class="person-title">Founder/President</p>
  </div>

  <p class="brand-name">Prairie Lantern Popcorn</p>
</section>

<section class="card card-back" aria-label="Business card back">
  <p class="brand-name">Prairie Lantern Popcorn</p>
  <p class="tagline">Popular for a reason</p>
  <p class="website">www.prairielanternpopcorn.com</p>
</section>

</body>
</html>
```